Concierge Healthcare Business Card Design and Logo

We need a logo and business card design for a new company called "Sound Haven". We will provide concierge audiological care, hearing aids, hearing exams, custom hearing protection etc to patients in the comfort of their homes and offices. We would like a sleek and modern design preferably with an Ear related logo.

Target Market(s)

People with hearing loss, Hunters, Musicians
My usual clientele are older individuals so usually 50+ years old

Industry/Entity Type

Health Care

Contact Information for Business Card

Celia Brandt, AuD
Audiologist
512-648-2917
soundhaven@mailvoro.com
www.soundhaven-vorel.com

Logo Text

Sound Haven

Number of Pages Required

3 page

```html
<!DOCTYPE html>
<html lang="en">
<head>
<meta charset="utf-8">
<title>Sound Haven – Business Card</title>
<link rel="stylesheet" href="https://fonts.googleapis.com/css2?family=Questrial&family=Source+Sans+3:wght@400;600&display=swap">
<style>
  :root {
    --bg-top: #2b2b2b;
    --bg-bottom: #050505;
    --card: #ffffff;
    --orange: #f0821e;
    --grey: #808080;
    --text: #4a4a4a;
  }
  * { margin: 0; padding: 0; box-sizing: border-box; }
  html, body { width: 1200px; height: 900px; overflow: hidden; }
  body {
    position: relative;
    background: linear-gradient(180deg, var(--bg-top) 0%, #1a1a1a 50%, var(--bg-bottom) 100%);
    font-family: "Source Sans 3", "Myriad Pro", Arial, sans-serif;
  }
  .card {
    position: absolute;
    top: 306px;
    width: 440px;
    height: 271px;
    background: var(--card);
    border-radius: 10px;
  }
  .card--front { left: 148px; }
  .card--back { left: 608px; }

  .front-brand {
    position: absolute;
    left: 40px;
    top: 116px;
    display: flex;
    align-items: center;
    gap: 8px;
    font-family: "Questrial", "Century Gothic", sans-serif;
    font-size: 25px;
    color: var(--orange);
    white-space: nowrap;
  }
  .brand-dot {
    width: 14px; height: 14px;
    border-radius: 50%;
    background: var(--grey);
  }

  .details {
    position: absolute;
    left: 239px;
    top: 68px;
    color: var(--text);
    font-size: 12.5px;
    line-height: 15px;
  }
  .details .name {
    color: var(--orange);
    font-weight: 600;
    font-size: 15px;
    line-height: 18px;
  }
  .details .address { margin-top: 11px; }
  .contacts { margin-top: 13px; list-style: none; }
  .contacts li { display: flex; align-items: center; gap: 6px; height: 16px; }
  .contacts svg { width: 9px; height: 9px; fill: var(--orange); flex: none; }

  .back-brand {
    position: absolute;
    left: 0; right: 0;
    top: 64px;
    display: flex;
    flex-direction: column;
    align-items: center;
  }
  .back-brand .brand-circle {
    width: 86px; height: 86px;
    border-radius: 50%;
    background: var(--orange);
  }
  .back-brand .brand-name {
    margin-top: 18px;
    font-family: "Questrial", "Century Gothic", sans-serif;
    font-size: 35px;
    color: var(--grey);
    letter-spacing: 0.3px;
  }
</style>
</head>
<body>
  <section class="card card--front">
    <div class="front-brand"><span class="brand-dot"></span>Sound Haven</div>
    <div class="details">
      <p class="name">Celia Brandt</p>
      <p class="title">Managing Director</p>
      <p class="address">12345, Address Goes Here<br>Country Name, 123456.</p>
      <ul class="contacts">
        <li><svg viewBox="0 0 10 10"><path d="M2 0.5 L3.6 2.6 L2.6 3.6 Q3.6 5.8 6.4 7.4 L7.4 6.4 L9.5 8 L8.2 9.5 Q1 8 0.5 1.8 Z"/></svg>512-648-2917</li>
        <li><svg viewBox="0 0 10 10"><rect x="0.5" y="2" width="9" height="6.5"/><path d="M0.5 2 L5 5.6 L9.5 2" stroke="#fff" stroke-width="0.9" fill="none"/></svg>soundhaven@mailvoro.com</li>
        <li><svg viewBox="0 0 10 10"><circle cx="5" cy="5" r="4.5"/><path d="M0.5 5 H9.5 M5 0.5 V9.5" stroke="#fff" stroke-width="0.7"/></svg>www.soundhaven-vorel.com</li>
      </ul>
    </div>
  </section>

  <section class="card card--back">
    <div class="back-brand">
      <span class="brand-circle"></span>
      <p class="brand-name">Sound Haven</p>
    </div>
  </section>
</body>
</html>
```